Website homepage rework for women's travel website

I have a homepage (http://www.ladies-at-the-helm.com) that I'm 50% happy with but don't want to completely overhaul. I'd like to retain a similar look but upgrade it to something a bit more modern and less old-fashioned. The basic sense of the site is empowering, self-confident, fun and adventurous - but female and over 40.

A number of the elements on the page have to be redesigned, a few can be tweaked, and a few left alone. See the rest of the brief for further information.

Target Market(s)

women over 40 who like to travel

Industry/Entity Type

Travel

Number of Pages Required

1 page

Font styles to use
Other font styles liked:
• see my brief

Requirements
Must have
• - size - the page must be significantly wider
• - the only font I MUST keep is Raleway (as in the tagline) and possibly the font of the site name (Ladies at the Helm). Both of those work for me. There are too many fonts on the page, however, and that needs to be unified.
• - the rectangles I click to get inside the site have to change to something more modern, possibly square - they do not have to be separated into two columns as they are now, nor do they need the titles (toolkit etc)
• - I like the background image of the header - but it needs to be wider of course - also keep in mind the aspect - it has to fit into the smaller inside pages, whose size will not change
• - at the end of the project I need to receive the separate elements of the design so I can eventually make a change myself if needed ie. replace my own photo, for example
Nice to have
• - the three photos need to change to something more eye-popping - or something else should take their place to fill the space
Should not have
• I do not want a full, original redesign. I want my readers to still feel as though they are on the same site - same header, mostly same fonts.

```html
<!DOCTYPE html>
<html lang="en">
<head>
<meta charset="utf-8">
<title>Ladies at the Helm</title>
<link rel="stylesheet" href="https://fonts.googleapis.com/css2?family=Raleway:wght@400;500;600;700&display=swap">
<style>
:root{
  --red:#c8300f;
  --orange:#e5781e;
  --ink:#333;
  --muted:#555;
  --band:#f1f1f1;
  --white:#fff;
}
*{margin:0;padding:0;box-sizing:border-box}
html,body{width:782px;height:1200px;overflow:hidden;background:var(--white)}
body{position:relative;font-family:"Raleway",sans-serif;color:var(--ink)}
.abs{position:absolute}
.hero{left:0;top:0;width:782px;height:400px;
  background:linear-gradient(180deg,#e98a1f 0%,#f3b043 22%,#d9742a 42%,#a5562b 55%,#8a6a3a 68%,#6a6050 82%,#5f5a4c 100%)}
.brand{left:247px;top:16px;width:286px;height:36px;background:var(--red);color:var(--white);font-size:26px;font-weight:500;text-align:center;line-height:36px;white-space:nowrap}
.tagline{left:240px;top:54px;width:300px;text-align:center;color:#fff;font-size:15.5px;font-weight:400;background:rgba(200,48,15,.85);line-height:20px;white-space:nowrap}
.nav{left:177px;top:88px;width:427px;height:29px;background:var(--white);display:flex;align-items:center;justify-content:space-around;padding:0 10px;font-size:8.5px;color:var(--muted);text-transform:uppercase;white-space:nowrap}
.nav .current{color:var(--red)}
.arrow{top:190px;width:14px;height:20px}
.intro{left:0;top:448px;width:782px;text-align:center;font-size:16.5px}
.pillar{top:486px;width:200px;text-align:center}
.pillar svg{display:block;margin:0 auto;height:24px}
.pillar h3{color:var(--red);font-size:16px;font-weight:700;margin-top:12px}
.pillar p{font-size:8.5px;line-height:11px;margin-top:5px;color:var(--ink)}
.cta{left:0;top:611px;width:782px;height:63px;background:var(--band)}
.cta-text{left:193px;top:630px;font-size:21.5px;color:var(--orange)}
.cta-btn{left:432px;top:629px;width:156px;height:28px;border:1px solid #aaa;font-size:10.5px;color:#888;text-align:center;line-height:26px}
.heading{left:0;width:782px;text-align:center;font-size:16px;font-weight:700}
.heading.red{color:var(--red)}
.heading.orange{color:var(--orange)}
.card{width:142px;text-align:center}
.card .thumb{height:96px}
.card h4{font-size:10.5px;font-weight:600;margin-top:10px;white-space:nowrap}
.card p{font-size:7px;margin-top:3px;color:var(--ink)}
.toolkit h4{color:var(--red)}
.dest h4{color:var(--orange)}
.footer{left:0;top:1137px;width:782px;height:63px;background:var(--band)}
.footer-links{left:86px;top:1154px;font-size:7px;color:var(--muted);word-spacing:1px}
.copyright{left:86px;top:1173px;font-size:7px;color:var(--muted)}
.social{top:1160px;width:16px;height:16px;border-radius:50%}
</style>
</head>
<body>
<div class="abs hero" role="img" aria-label="Desert road with red mesas under an orange sky, the author's portrait with travel snapshots at the centre"></div>
<div class="abs brand">Ladies at the Helm</div>
<div class="abs tagline">For women who travel smart, safe + solo</div>
<nav class="abs nav">
  <span class="current">Start Here</span><span>About</span><span>Travel Resources</span><span>Blog</span><span>Travel Shop</span><span>Contact</span>
  <svg width="8" height="8" viewBox="0 0 10 10"><circle cx="4" cy="4" r="3" fill="none" stroke="#777" stroke-width="1.4"/><line x1="6.3" y1="6.3" x2="9" y2="9" stroke="#777" stroke-width="1.4"/></svg>
</nav>
<svg class="abs arrow" style="left:16px" viewBox="0 0 14 20"><polyline points="11,2 3,10 11,18" fill="none" stroke="rgba(255,255,255,.6)" stroke-width="2"/></svg>
<svg class="abs arrow" style="left:752px" viewBox="0 0 14 20"><polyline points="3,2 11,10 3,18" fill="none" stroke="rgba(255,255,255,.6)" stroke-width="2"/></svg>

<p class="abs intro">Hi, I'm Marta. I took my first solo trip at 15. I'll show you how to travel...</p>

<div class="abs pillar" style="left:80px">
  <svg viewBox="0 0 20 26"><path d="M10 2a7 7 0 0 0-4 12.7V18h8v-3.3A7 7 0 0 0 10 2z" fill="none" stroke="#c8300f" stroke-width="2"/><rect x="6.5" y="20" width="7" height="2" fill="#c8300f"/><rect x="7.5" y="23" width="5" height="2" fill="#c8300f"/></svg>
  <h3>Smart</h3><p>Practical tools to help you plan – and afford –<br>the perfect trip</p>
</div>
<div class="abs pillar" style="left:290px">
  <svg viewBox="0 0 20 26"><path d="M2 2h16v11c0 6-8 11-8 11S2 19 2 13z" fill="#c8300f"/><path d="M10 5v16c3-2 5-5 5-8V5z" fill="#fff"/></svg>
  <h3>Safe</h3><p>Down-to-earth advice and a ton of safety<br>recommendations</p>
</div>
<div class="abs pillar" style="left:502px">
  <svg viewBox="0 0 22 24"><circle cx="11" cy="6" r="5.5" fill="#c8300f"/><path d="M1 24v-5a6 6 0 0 1 6-6h8a6 6 0 0 1 6 6v5z" fill="#c8300f"/></svg>
  <h3>Solo</h3><p>yes, you can do it!</p>
</div>

<div class="abs cta"></div>
<div class="abs cta-text">Thinking of solo travel?</div>
<div class="abs cta-btn">Click here to find out how</div>

<h2 class="abs heading red" style="top:722px">Travel Toolkit</h2>
<div class="abs card toolkit" style="left:86px;top:758px"><div class="thumb" role="img" aria-label="Plated lamb chops with vegetables" style="background:linear-gradient(135deg,#f3ead8,#8a4a22 60%,#d9d2c2)"></div><h4>Eating With Locals</h4><p>The ultimate guide to social dining</p></div>
<div class="abs card toolkit" style="left:242px;top:758px"><div class="thumb" role="img" aria-label="Open suitcase packed with pink clothes" style="background:linear-gradient(90deg,#8c8f94,#d9d2cf 45%,#e0626a 60%,#c95560)"></div><h4>Your Packing List</h4><p>Take what you need - no more</p></div>
<div class="abs card toolkit" style="left:398px;top:758px"><div class="thumb" role="img" aria-label="Rolled banknotes and a small globe" style="background:linear-gradient(135deg,#e7e2d2,#c9c7b4 50%,#b8b8a8)"></div><h4>No Single Supplement</h4><p>17 ways to avoid paying it</p></div>
<div class="abs card toolkit" style="left:554px;top:758px"><div class="thumb" role="img" aria-label="Woman with a backpack walking through a green meadow" style="background:linear-gradient(180deg,#7aa64a,#5c8a34 60%,#91b25a)"></div><h4>Stress Management Course</h4><p>How to travel stress-free</p></div>

<h2 class="abs heading orange" style="top:930px">Destinations</h2>
<div class="abs card dest" style="left:86px;top:966px"><div class="thumb" role="img" aria-label="Waterfalls surrounded by jungle" style="background:linear-gradient(180deg,#9fb8c8,#e4ecef 40%,#3f6b3a 75%,#2f5130)"></div><h4>Solo In Argentina</h4><p>Does it really take two to tango?</p></div>
<div class="abs card dest" style="left:242px;top:966px"><div class="thumb" role="img" aria-label="Misty rolling hills at sunrise" style="background:linear-gradient(180deg,#d9c07a,#e4dcb9 30%,#7c9a3a 65%,#4f7626)"></div><h4>Europe For Foodies</h4><p>9 top destinations to try in October</p></div>
<div class="abs card dest" style="left:398px;top:966px"><div class="thumb" role="img" aria-label="Cheerful traveller under palm trees and blue sky" style="background:linear-gradient(180deg,#5fa0dc,#b7d7ef 50%,#6f9a45)"></div><h4>Solo Female Travel</h4><p>A 3-week Central Asia itinerary</p></div>
<div class="abs card dest" style="left:554px;top:966px"><div class="thumb" role="img" aria-label="Aerial view of a lakeside city with bridges" style="background:linear-gradient(180deg,#9ab6cf,#b8a99a 40%,#3f7c8c 70%,#2f6577)"></div><h4>Rebellious Carouge</h4><p>Geneva's Alter Ego?</p></div>

<footer class="abs footer"></footer>
<div class="abs footer-links">Start Here &nbsp;| &nbsp;About &nbsp;| &nbsp;Travel Resources &nbsp;| &nbsp;Blog &nbsp;| &nbsp;Travel Shop &nbsp;| &nbsp;Contact</div>
<div class="abs copyright">Copyright © 2016 &nbsp;Company name. &nbsp;All rights reserved.</div>
<span class="abs social" style="left:572px;background:#3b5a9a"></span>
<span class="abs social" style="left:594px;background:#2ea3e0"></span>
<span class="abs social" style="left:616px;background:#c8202c"></span>
<span class="abs social" style="left:638px;background:#f07a1a"></span>
<span class="abs social" style="left:660px;background:#d8261e"></span>
<span class="abs social" style="left:682px;background:#4a6f95"></span>
</body>
</html>
```